Tallowmere Air Business Card Design

Design new, 2 sides, business cards for a residential and light commercial heating, air conditioning contractor.

Target Market(s)

Homeowners, small businesses

Industry/Entity Type

Business

Contact Information for Business Card

Dominic Westerhall
Phone - 862-415-2736
Email
Address - PO box 518
Brightwater NJ 07912
Website - www.HarborBreezeLLC.example

Requirements
Must have
• logo, company colors, standard size with no die cut, so I can use nova stamp

```html
<!DOCTYPE html>
<html lang="en">
<head>
<meta charset="utf-8">
<title>Tallowmere Air Business Card</title>
<link rel="stylesheet" href="https://fonts.googleapis.com/css2?family=Crimson+Text:wght@400;600&family=Open+Sans:wght@400;600&display=swap">
<style>
  :root {
    --stage-top: #080808;
    --stage-bottom: #353535;
    --card-top: #3b3b3b;
    --card-bottom: #000000;
    --ink: #ffffff;
    --ink-soft: #c4c4c4;
  }
  * { margin: 0; padding: 0; box-sizing: border-box; }
  html, body { width: 1200px; height: 900px; overflow: hidden; }
  body {
    background: linear-gradient(180deg, var(--stage-top) 0%, var(--stage-bottom) 100%);
    position: relative;
    font-family: "Open Sans", Arial, sans-serif;
    color: var(--ink);
  }
  .card {
    position: absolute;
    width: 347px;
    height: 561px;
    background: linear-gradient(180deg, var(--card-top) 0%, #151515 45%, var(--card-bottom) 100%);
    text-align: center;
  }
  .card-front { left: 263px; top: 170px; }
  .card-back  { left: 649px; top: 169px; }
  .brand-name {
    position: absolute;
    left: 0; right: 0;
    font-family: "Crimson Text", Georgia, serif;
    font-weight: 600;
    font-size: 44px;
    line-height: 1.02;
    letter-spacing: 0.5px;
    color: var(--ink);
  }
  .card-front .brand-name { top: 82px; }
  .card-back .brand-name { top: 322px; }
  .person-name {
    position: absolute; left: 0; right: 0; top: 294px;
    font-family: "Crimson Text", Georgia, serif;
    font-size: 26px;
    letter-spacing: 1px;
    text-transform: uppercase;
    white-space: nowrap;
  }
  .person-title {
    position: absolute; left: 0; right: 0; top: 326px;
    font-size: 17px;
  }
  .contact-list {
    position: absolute; left: 0; right: 0; top: 385px;
    list-style: none;
    font-size: 14.5px;
    line-height: 21px;
  }
  .contact-list b { font-weight: 600; font-size: 17px; }
  .postal-address {
    position: absolute; left: 0; right: 0; top: 488px;
    font-style: normal;
    font-size: 14.5px;
    line-height: 22px;
  }
  .website {
    position: absolute; left: 0; right: 0; top: 506px;
    font-size: 16px;
    color: var(--ink-soft);
    white-space: nowrap;
  }
</style>
</head>
<body>
  <section class="card card-front">
    <div class="brand-name">Tallowmere<br>Air</div>
    <div class="person-name">Dominic Westerhall</div>
    <div class="person-title">Director</div>
    <ul class="contact-list">
      <li><b>p:</b> 862-415-2736</li>
      <li><b>f:</b> 862-415-2736</li>
      <li><b>e:</b> info@tallowmereair.example</li>
    </ul>
    <address class="postal-address">PO box 518<br>Brightwater NJ 07912</address>
  </section>

  <section class="card card-back">
    <div class="brand-name">Tallowmere<br>Air</div>
    <div class="website">www.TallowmereAirLLC.example</div>
  </section>
</body>
</html>
```